Animal Eye Clinic needs a Business card

We are a new veterinary ophthalmology practice (Ridgeline Pet Vision Care) and we need a business card designed. We only see animal eyes - we are not a regular veterinary clinic. We already have a logo. We are looking for a professional, good looking business card to hand out to our clients. We are looking for something simple but professional and contemporary. Our logo is likely the only picture/graphic that needs to be on the card.
Updates

Contact Information for Business Card

Delia Vossman, BSc, DVM, MSc, DipACVO
Veterinary Ophthalmologist

Phone: 250.418.3927
Email: ridgelinepetvisioncare@mailbox-example.net
Website: ridgelinepetvisioncare-example.net
Address: 1874 Thornbury Rd
Kelowna, BC, V1X 4M9

Colors

Designer to choose colors to be used in the design.

Requirements
Must have
• Our logo (attached)

```html
<!DOCTYPE html>
<html lang="en">
<head>
<meta charset="utf-8">
<title>Ridgeline Pet Vision Care – Business Card</title>
<link rel="stylesheet" href="https://fonts.googleapis.com/css2?family=Montserrat:wght@300;400;600;700&family=Quicksand:wght@400;500&display=swap">
<style>
  :root {
    --teal: #1f97a6;
    --grey: #7b7b7b;
    --grey-tab: #8a8a8a;
    --card: #f7f7f7;
    --page: #e4e2df;
    --shadow: rgba(0, 0, 0, 0.14);
  }
  * { box-sizing: border-box; margin: 0; padding: 0; }
  html, body { width: 1200px; height: 900px; overflow: hidden; }
  body {
    background: var(--page);
    display: flex;
    flex-direction: column;
    align-items: center;
    justify-content: center;
    gap: 40px;
  }
  .card {
    position: relative;
    width: 680px;
    height: 389px;
    background: var(--card);
    box-shadow: 0 8px 24px var(--shadow);
    overflow: hidden;
  }

  /* Contact side */
  .card--contact .tab {
    position: absolute;
    left: 0; top: 40px;
    width: 14px; height: 64px;
    background: var(--grey-tab);
    border-radius: 0 10px 10px 0;
  }
  .identity {
    position: absolute;
    left: 40px; top: 36px;
    font-family: "Montserrat", sans-serif;
  }
  .identity .name {
    font-size: 30px;
    letter-spacing: 0.12em;
    line-height: 1;
    text-transform: uppercase;
  }
  .identity .first { color: var(--teal); font-weight: 700; }
  .identity .last { color: var(--grey); font-weight: 300; }
  .identity .role,
  .identity .credentials {
    color: var(--grey);
    font-size: 13px;
    font-weight: 400;
    letter-spacing: 0.06em;
    text-transform: uppercase;
    line-height: 1.35;
  }
  .identity .role { margin-top: 6px; }

  .contact-list {
    position: absolute;
    right: 30px; top: 140px;
    list-style: none;
    font-family: "Quicksand", sans-serif;
    font-size: 14px;
    color: var(--grey);
    letter-spacing: 0.08em;
  }
  .contact-list li {
    display: flex;
    align-items: center;
    justify-content: flex-end;
    gap: 12px;
    height: 34px;
  }
  .icon {
    width: 24px; height: 24px;
    border-radius: 6px;
    background: var(--teal);
    display: flex;
    align-items: center;
    justify-content: center;
    flex-shrink: 0;
  }
  .icon svg { width: 14px; height: 14px; }

  .practice-mark {
    position: absolute;
    left: 56px; bottom: 48px;
    display: flex;
    align-items: center;
    gap: 12px;
  }
  .mark-dot {
    border-radius: 50%;
    background: var(--teal);
    flex-shrink: 0;
  }
  .practice-mark .mark-dot { width: 26px; height: 26px; }
  .practice-name {
    font-family: "Montserrat", sans-serif;
    font-weight: 600;
    color: var(--teal);
    letter-spacing: 0.02em;
  }
  .practice-mark .practice-name { font-size: 18px; }

  /* Brand side */
  .card--brand .brand-lockup {
    position: absolute;
    left: 0; right: 0; top: 140px;
    display: flex;
    align-items: center;
    justify-content: center;
    gap: 18px;
  }
  .card--brand .mark-dot { width: 48px; height: 48px; }
  .card--brand .practice-name { font-size: 36px; }
  .website {
    position: absolute;
    left: 0; right: 0; bottom: 48px;
    text-align: center;
    font-family: "Quicksand", sans-serif;
    font-size: 20px;
    color: var(--teal);
    letter-spacing: 0.14em;
  }
</style>
</head>
<body>

  <section class="card card--contact" aria-label="Business card, contact side">
    <div class="tab"></div>
    <header class="identity">
      <p class="name"><span class="first">Delia</span> <span class="last">Vossman</span></p>
      <p class="role">Veterinary Ophthalmologist</p>
      <p class="credentials">BSc, DVM, MSc, DipACVO</p>
    </header>

    <ul class="contact-list">
      <li>250.418.3927
        <span class="icon"><svg viewBox="0 0 24 24" fill="#fff"><path d="M6.6 10.8a15.1 15.1 0 0 0 6.6 6.6l2.2-2.2a1 1 0 0 1 1-.25 11.4 11.4 0 0 0 3.6.57 1 1 0 0 1 1 1V20a1 1 0 0 1-1 1A17 17 0 0 1 3 4a1 1 0 0 1 1-1h3.5a1 1 0 0 1 1 1c0 1.25.2 2.45.57 3.6a1 1 0 0 1-.25 1z"/></svg></span>
      </li>
      <li>1874 Thornbury Rd Kelowna, BC, V1X 4M9
        <span class="icon"><svg viewBox="0 0 24 24" fill="#fff"><path d="M12 2a7 7 0 0 0-7 7c0 5.2 7 13 7 13s7-7.8 7-13a7 7 0 0 0-7-7zm0 9.5A2.5 2.5 0 1 1 12 6.5a2.5 2.5 0 0 1 0 5z"/></svg></span>
      </li>
      <li>ridgelinepetvisioncare@mailbox-example.net
        <span class="icon"><svg viewBox="0 0 24 24" fill="#fff"><path d="M2 11 22 3l-7 19-3.5-8z"/></svg></span>
      </li>
      <li>ridgelinepetvisioncare-example.net
        <span class="icon"><svg viewBox="0 0 24 24" fill="none" stroke="#fff" stroke-width="2"><circle cx="12" cy="12" r="9"/><path d="M3 12h18M12 3c3 3 3 15 0 18M12 3c-3 3-3 15 0 18"/></svg></span>
      </li>
    </ul>

    <div class="practice-mark">
      <span class="mark-dot"></span>
      <span class="practice-name">Ridgeline Pet Vision Care</span>
    </div>
  </section>

  <section class="card card--brand" aria-label="Business card, brand side">
    <div class="brand-lockup">
      <span class="mark-dot"></span>
      <span class="practice-name">Ridgeline Pet Vision Care</span>
    </div>
    <p class="website">ridgelinepetvisioncare-example.net</p>
  </section>

</body>
</html>
```